Home Security Company Business Card

Looking for a eye catching business card that is non traditional and stands out but yet still looks professional. It should include all the pertinent information such as name, title, address, telephone, e-mail, website address should definitely stand out and then finally the logo.

Target Market(s)

Residential and Commercial accounts mostly upscale accounts

Industry/Entity Type

Security

Contact Information for Business Card

Name
Title
Address
Office #
Cell #
E-mail
Website

Font styles to use
Serif
Sans Serif

Requirements
Must have
• Logo, two sided color configuration
Nice to have
• You decide
Should not have
• There really aren't any.

```html
<!DOCTYPE html>
<html lang="en">
<head>
<meta charset="utf-8">
<title>Ironvale Security Systems – Business Card</title>
<link rel="stylesheet" href="https://fonts.googleapis.com/css2?family=Montserrat:wght@400;500;600&display=swap">
<style>
  :root {
    --backdrop: #3a322d;
    --card-black: #161616;
    --card-black-soft: #222222;
    --gold: #f3bf3f;
    --text-grey: #b9b9b9;
    --text-light: #e6e6e6;
  }
  * { box-sizing: border-box; margin: 0; padding: 0; }
  html, body {
    width: 1200px; height: 844px; overflow: hidden;
    background: var(--backdrop);
    font-family: "Montserrat", Arial, sans-serif;
  }
  .stage {
    position: relative; width: 1200px; height: 844px;
    display: flex; align-items: center; justify-content: center; gap: 40px;
  }
  .card {
    position: relative; width: 540px; height: 309px;
    background: linear-gradient(135deg, var(--card-black-soft), var(--card-black));
    overflow: hidden;
    box-shadow: 0 14px 30px rgba(0,0,0,0.45);
  }
  /* Front side */
  .card-front::before, .card-front::after {
    content: ""; position: absolute; left: 0; right: 0; height: 12px;
    background: var(--gold);
  }
  .card-front::before { top: 0; }
  .card-front::after { bottom: 0; }
  .holder {
    position: absolute; left: 190px; top: 62px; text-align: center;
  }
  .holder-name {
    color: var(--gold); font-weight: 600; font-size: 17px; letter-spacing: 0.5px;
    padding-bottom: 3px; border-bottom: 1px solid var(--gold);
  }
  .holder-title {
    color: var(--text-grey); font-size: 13px; margin-top: 3px;
  }
  .contacts {
    position: absolute; left: 0; right: 0; top: 150px;
    list-style: none; text-align: center;
    color: var(--text-light); font-size: 13px; line-height: 19px;
  }
  .contacts li { display: flex; align-items: center; justify-content: center; gap: 6px; }
  .contacts svg { width: 10px; height: 10px; fill: var(--gold); }
  .address {
    position: absolute; left: 0; right: 0; top: 240px; text-align: center;
    color: var(--text-grey); font-size: 13px;
  }
  /* Back side */
  .tab {
    position: absolute; width: 24px; height: 16px; background: var(--gold);
    border-right: 4px solid #d9d9d9;
  }
  .tab-left { left: 0; top: 150px; }
  .tab-right { right: 0; top: 20px; border-right: none; border-left: 4px solid #d9d9d9; }
  .brand {
    position: absolute; inset: 0; display: flex; align-items: center; justify-content: center; gap: 12px;
    color: var(--gold); font-weight: 600; font-size: 22px; letter-spacing: 1px;
  }
  .brand-mark { width: 16px; height: 16px; border-radius: 50%; background: var(--gold); }
</style>
</head>
<body>
<main class="stage">
  <section class="card card-front" aria-label="Card front">
    <div class="holder">
      <p class="holder-name">MARCUS HALE</p>
      <p class="holder-title">Managing Director</p>
    </div>
    <ul class="contacts">
      <li><svg viewBox="0 0 10 10"><path d="M2 1h2l1 2-1 1a5 5 0 0 0 2 2l1-1 2 1v2c0 1-1 1-1 1A8 8 0 0 1 1 2s0-1 1-1z"/></svg>044-555-0142</li>
      <li><svg viewBox="0 0 10 10"><path d="M3 0h4a1 1 0 0 1 1 1v8a1 1 0 0 1-1 1H3a1 1 0 0 1-1-1V1a1 1 0 0 1 1-1zm0 1.5v6h4v-6z"/></svg>123-555-0178</li>
      <li><svg viewBox="0 0 10 10"><path d="M0 2h10v6H0zm1 1 4 3 4-3"/></svg>marcus@ironvalesecure.com</li>
      <li><svg viewBox="0 0 10 10"><path d="M4 6 6 4M3 5 1.5 6.5a1.5 1.5 0 0 0 2 2L5 7M7 5l1.5-1.5a1.5 1.5 0 0 0-2-2L5 3" stroke="#f3bf3f" stroke-width="1.2" fill="none"/></svg>www.ironvalesecure.com</li>
    </ul>
    <p class="address">88 Harbor Lane | Westbrook, AB | 204518</p>
  </section>

  <section class="card card-back" aria-label="Card back">
    <span class="tab tab-left"></span>
    <span class="tab tab-right"></span>
    <div class="brand"><span class="brand-mark"></span>IRONVALE SECURITY SYSTEMS INC.</div>
  </section>
</main>
</body>
</html>
```